Lantern Co. Supplement General Packaging Design

I am looking for a design template to design all of my various supplements and other products around. Meaning that this design should be able to just be able to change around words, up to a few small images, and text to suit my other various products.

The brand name is Lantern Co. and the slogan is: Heros Are Made
This is For an Apple Cider Vinegar Gummy, and include these top three things: Vegan, Gluten Free, Non-GMO somewhere in the design.

I want the design to have a luxurious feel. With some kind of design element where the logo is sort of the secondary aspect of the design.

Target Market(s)

Men age 24-45

Industry/Entity Type

Supplement

Requirements
Must have
• MUST HAVE A "vintage" LOOK AND FEEL. MUST HAVE ANOTHER design element besides the logo. (Something Vintage) MUST USE THE PROVIDED TEMPLATE A PDF IN THE FILES BELOW LABELED " TEMPLATE" and the LOGO PROVIDED under "Lantern Co. 2" OR "lantern co.3" whichever is better suited for the design. Bold design. Another color besides black to stand out. Use the lantern co logo which is below in the provided images. The design should go around the logo and fit the same aesthetic. The rest are for inspiration, what I like.

```html
<!DOCTYPE html>
<html lang="en">
<head>
<meta charset="utf-8">
<title>Lantern Co. — Supplement Label</title>
<link rel="stylesheet" href="https://fonts.googleapis.com/css2?family=Jost:wght@200;400;500&display=swap">
<style>
  :root {
    --ink: #141414;
    --gold: #d9b44a;
    --gold-light: #f6e27a;
    --gold-deep: #b8862b;
  }
  html, body {
    margin: 0;
    padding: 0;
    width: 1200px;
    height: 1200px;
    overflow: hidden;
    background: var(--ink);
  }
  .label {
    position: relative;
    width: 1200px;
    height: 1200px;
    background: var(--ink);
    font-family: "Jost", sans-serif;
    color: var(--gold);
  }
  .label__frame {
    position: absolute;
    inset: 0;
  }
  .label__emblem {
    position: absolute;
    left: 447px;
    top: 294px;
    width: 306px;
    height: 306px;
    border-radius: 50%;
    box-sizing: border-box;
    border: 9px solid var(--gold);
    background: radial-gradient(circle, var(--ink) 0 30%, #4a3a16 45%, #8a6a2a 62%, #3a2e12 80%, var(--ink) 100%);
  }
  .label__brand {
    position: absolute;
    left: 0;
    right: 0;
    top: 628px;
    margin: 0;
    text-align: center;
    font-weight: 200;
    font-size: 84px;
    line-height: 1;
    letter-spacing: 2px;
    text-transform: uppercase;
  }
  .label__slogan {
    position: absolute;
    left: 0;
    right: 0;
    top: 768px;
    margin: 0;
    text-align: center;
    font-weight: 400;
    font-size: 28px;
    line-height: 1;
    text-transform: uppercase;
  }
  .label__claims {
    position: absolute;
    left: 0;
    right: 0;
    top: 857px;
    margin: 0;
    text-align: center;
    font-weight: 500;
    font-size: 18px;
    line-height: 1;
    text-transform: uppercase;
  }
</style>
</head>
<body>
<main class="label">
  <svg class="label__frame" width="1200" height="1200" viewBox="0 0 1200 1200" aria-hidden="true">
    <defs>
      <linearGradient id="goldSheen" x1="0" y1="0" x2="1" y2="1">
        <stop offset="0" stop-color="#f6e27a"/>
        <stop offset="0.35" stop-color="#c9992f"/>
        <stop offset="0.6" stop-color="#f3d77a"/>
        <stop offset="1" stop-color="#b8862b"/>
      </linearGradient>
    </defs>
    <g class="frame-lines" fill="none" stroke="url(#goldSheen)">
      <path stroke-width="5" d="M214.5 112.5 H985.5 A102 102 0 0 0 1087.5 214.5 V985.5 A102 102 0 0 0 985.5 1087.5 H214.5 A102 102 0 0 0 112.5 985.5 V214.5 A102 102 0 0 0 214.5 112.5 Z"/>
      <path stroke-width="3" d="M223.5 130.5 H976.5 A93 93 0 0 0 1069.5 223.5 V976.5 A93 93 0 0 0 976.5 1069.5 H223.5 A93 93 0 0 0 130.5 976.5 V223.5 A93 93 0 0 0 223.5 130.5 Z"/>
      <path stroke-width="3" d="M232.5 145.5 H967.5 A87 87 0 0 0 1054.5 232.5 V967.5 A87 87 0 0 0 967.5 1054.5 H232.5 A87 87 0 0 0 145.5 967.5 V232.5 A87 87 0 0 0 232.5 145.5 Z"/>
    </g>
    <g class="slogan-rules" fill="none" stroke="url(#goldSheen)" stroke-width="2.5">
      <line x1="175" y1="783" x2="390" y2="783"/>
      <circle cx="400" cy="783" r="10"/>
      <line x1="410" y1="783" x2="435" y2="783"/>
      <line x1="762" y1="783" x2="785" y2="783"/>
      <circle cx="795" cy="783" r="10"/>
      <line x1="805" y1="783" x2="1017" y2="783"/>
    </g>
  </svg>

  <div class="label__emblem" role="img" aria-label="Gold geometric circular ornament emblem"></div>

  <h1 class="label__brand">Lantern Co.</h1>
  <p class="label__slogan">Heros Are Made</p>
  <p class="label__claims">Vegan, Gluten Free &amp; Non-GMO Supplement</p>
</main>
</body>
</html>
```